New clean and fresh corporate PPT template for Telecom equipment maker

MPK (VORQEX MPKT) is a telecom equipment maker in Silicon Valley. Our current PPT template that goes with http://peltrovane.com is overbuilt, dark, huge in file size, and looks the opposite of fresh and clean.
Our new microsite @ http://investor-mpkt.com is the direction we want to go. We are B2B, selling to telecom operators, but still want something that looks clean and fresh and not stuffy, hence primarily white background with maximum whitespace in 16:9 format.
Style guidelines attached, exclusive use of approved colors required, the master should remain as simple as possible, and we want the file size to stay reasonable (i.e. less is better). Features we would like include:
- Lato font built-in to the template
- Text boxes with standard size fonts, that automatically get smaller with indention
- An interesting bullet style, nothing crazy, but with visual interest
- A pre-selected table format that is clean and allows for high-density tables with many rows & columns
- Whichever standard slides layouts in the master you think would help result in slides that are found in the current deck, without someone needing to build their own slide

```html
<!DOCTYPE html>
<html lang="en">
<head>
<meta charset="utf-8">
<title>Accelerated Network Bandwidth Demands</title>
<link href="https://fonts.googleapis.com/css2?family=Lato:wght@400;700&family=Roboto:wght@400;500;700&display=swap" rel="stylesheet">
<style>
  :root {
    --ink-title: #4a5a6c;
    --ink-heading: #2f3c4a;
    --ink-body: #555b61;
    --ink-highlight: #1c6a8a;
    --teal: #45c2c0;
    --lime: #8dc63f;
    --coral: #f0625d;
    --bar: #1d5a70;
    --cagr: #8dbf4a;
    --callout: #edb021;
    --callout-text: #fdf0cc;
    --grid: #e3e3e3;
    --frame: #d8d8d8;
    --icon-fill: #e3f2f4;
    --brand-grey: #c4c4c4;
  }
  * { box-sizing: border-box; margin: 0; padding: 0; }
  html, body { width: 1200px; height: 675px; overflow: hidden; background: #fff; }
  .slide { position: relative; width: 1200px; height: 675px; background: #fff; font-family: "Roboto", Arial, sans-serif; }

  .slide-title {
    position: absolute; top: 34px; left: 0; width: 100%;
    text-align: center; font-family: "Lato", Arial, sans-serif; font-weight: 700;
    font-size: 45px; color: var(--ink-title); letter-spacing: -0.2px;
  }
  .title-accent { position: absolute; top: 101px; left: 537px; display: flex; height: 5px; }
  .title-accent span { width: 42px; height: 5px; }
  .title-accent .a1 { background: var(--teal); }
  .title-accent .a2 { background: var(--lime); }
  .title-accent .a3 { background: var(--coral); }

  .section-heading {
    position: absolute; top: 116px; left: 39px;
    font-family: "Lato", Arial, sans-serif; font-weight: 700; font-size: 23px; color: var(--ink-heading);
  }

  .demand { position: absolute; width: 230px; text-align: center; color: var(--ink-body); font-size: 16px; line-height: 19.6px; white-space: nowrap; }
  .demand-icon { margin: 0 auto 12px; width: 60px; height: 64px; border-radius: 10px; background: var(--icon-fill); }
  .demand h3 { font-size: 16px; font-weight: 700; color: #4c5359; margin-bottom: 0; }
  .demand em { font-style: normal; color: var(--ink-highlight); }
  .d1 { left: 19px; top: 174px; }
  .d2 { left: 231px; top: 166px; }
  .d3 { left: 468px; top: 172px; }
  .d4 { left: 720px; top: 168px; }
  .d5 { left: 957px; top: 152px; }
  .d1 .demand-icon { width: 54px; height: 62px; }
  .d3 .demand-icon { width: 100px; height: 60px; border-radius: 30px; }
  .d5 .demand-icon { width: 78px; height: 90px; }

  .chart-panel { position: absolute; left: 211px; top: 351px; width: 521px; height: 266px; border: 1.5px solid var(--frame); }
  .chart-panel svg { position: absolute; left: 0; top: 0; }

  .callout { position: absolute; left: 737px; top: 403px; width: 247px; height: 152px; }
  .callout-text {
    position: absolute; left: 42px; top: 0; width: 205px; height: 152px;
    display: flex; align-items: center; justify-content: center; text-align: center;
    color: var(--callout-text); font-size: 21px; line-height: 21.5px;
  }

  .brand { position: absolute; left: 16px; top: 621px; display: flex; align-items: center; gap: 8px; }
  .brand-mark { width: 14px; height: 14px; background: var(--brand-grey); }
  .brand-name { font-family: "Lato", Arial, sans-serif; font-weight: 700; font-size: 30px; color: var(--brand-grey); }

  .copyright { position: absolute; left: 0; width: 1160px; top: 643px; text-align: center; font-family: "Lato", Arial, sans-serif; font-size: 14.5px; color: #5d646a; }
  .page-rule { position: absolute; left: 1125px; top: 623px; width: 75px; height: 4px; background: var(--teal); }
  .page-number { position: absolute; left: 1126px; top: 636px; font-size: 19px; color: #444; }
</style>
</head>
<body>
<main class="slide">
  <h1 class="slide-title">Accelerated Network Bandwidth Demands</h1>
  <div class="title-accent"><span class="a1"></span><span class="a2"></span><span class="a3"></span></div>

  <h2 class="section-heading">Network Demands of High Bandwidth as below</h2>

  <section class="demand d1">
    <div class="demand-icon" role="img" aria-label="Outline icon of a data storage stack"></div>
    <h3>Data and video</h3>
    <p>Video will represent <em>82% of</em><br><em>all IP traffic</em> in 2021</p>
  </section>
  <section class="demand d2">
    <div class="demand-icon" role="img" aria-label="Outline icon of a broadcast antenna tower"></div>
    <h3>Mobile and 4GLTE/5G</h3>
    <p>Wireless and mobile device<br>traffic <em>more than 63% of</em><br><em>total IP traffic</em> by 2021</p>
  </section>
  <section class="demand d3">
    <div class="demand-icon" role="img" aria-label="Outline icon of a cloud with wireless signal"></div>
    <h3>Cloud Services</h3>
    <p>By 2020, 92% of all data<br>center traffic will come from<br>the cloud</p>
  </section>
  <section class="demand d4">
    <div class="demand-icon" role="img" aria-label="Outline icon of a direction signpost"></div>
    <h3>Changing Traffic Patterns</h3>
    <p>Smartphone traffic <em>will</em><br><em>exceed</em> PC traffic by 2021</p>
  </section>
  <section class="demand d5">
    <div class="demand-icon" role="img" aria-label="Outline icons of a car, smartwatch and light bulb"></div>
    <h3>“Internet of Things”</h3>
    <p>The number of devices<br>connected to IP networks<br>will be <em>3x as high as the</em><br><em>global population</em> in 2021</p>
  </section>

  <figure class="chart-panel">
    <svg width="521" height="266" viewBox="0 0 521 266" font-family="Roboto, Arial, sans-serif">
      <text x="259" y="22" text-anchor="middle" font-size="15" font-weight="500" fill="#3d4348">Global IP Traffic Growth, 2016-2021</text>
      <g stroke="var(--grid)" stroke-width="1">
        <line x1="64" y1="55" x2="408" y2="55"/>
        <line x1="64" y1="82" x2="408" y2="82"/>
        <line x1="64" y1="109" x2="408" y2="109"/>
        <line x1="64" y1="136" x2="408" y2="136"/>
        <line x1="64" y1="163" x2="408" y2="163"/>
        <line x1="64" y1="190" x2="408" y2="190"/>
        <line x1="64" y1="217" x2="408" y2="217"/>
      </g>
      <g font-size="12" fill="#555" text-anchor="end">
        <text x="54" y="59">300</text>
        <text x="54" y="86">250</text>
        <text x="54" y="113">200</text>
        <text x="54" y="140">150</text>
        <text x="54" y="167">100</text>
        <text x="54" y="194">50</text>
        <text x="54" y="221">0</text>
      </g>
      <rect x="75" y="55" width="111" height="44" fill="var(--cagr)"/>
      <text x="130" y="74" text-anchor="middle" font-size="13" font-weight="700" fill="#fff">24% CAGR</text>
      <text x="130" y="91" text-anchor="middle" font-size="12" fill="#fff">2016-2021</text>
      <g fill="var(--bar)">
        <rect x="71" y="165" width="35" height="52"/>
        <rect x="129" y="151" width="35" height="66"/>
        <rect x="187" y="136" width="35" height="81"/>
        <rect x="246" y="116" width="35" height="101"/>
        <rect x="304" y="94" width="35" height="123"/>
        <rect x="362" y="67" width="35" height="150"/>
      </g>
      <g font-size="11.5" font-weight="700" fill="#fff" text-anchor="middle">
        <text x="88" y="198">96.1</text>
        <text x="147" y="184">121.7</text>
        <text x="205" y="176">150.9</text>
        <text x="264" y="163">186.4</text>
        <text x="322" y="150">228.4</text>
        <text x="380" y="137">278.1</text>
      </g>
      <g font-size="12" fill="#555" text-anchor="middle">
        <text x="88" y="238">2016</text>
        <text x="147" y="238">2017</text>
        <text x="205" y="238">2018</text>
        <text x="264" y="238">2019</text>
        <text x="322" y="238">2020</text>
        <text x="380" y="238">2021</text>
      </g>
      <rect x="424" y="144" width="7" height="7" fill="var(--bar)"/>
      <text x="434" y="151" font-size="12" fill="#555">Exabytes</text>
      <text x="434" y="166" font-size="12" fill="#555">per Month</text>
    </svg>
  </figure>

  <div class="callout">
    <svg width="247" height="152" viewBox="0 0 247 152">
      <polygon points="0,70 42,27 42,0 247,0 247,152 42,152 42,113" fill="var(--callout)"/>
    </svg>
    <p class="callout-text">Global IP traffic<br>expected to<br>increase ~3x from<br>2016 to 2021</p>
  </div>

  <footer>
    <div class="brand">
      <span class="brand-mark"></span>
      <span class="brand-name">MPK</span>
    </div>
    <p class="copyright">© 2018 Peltrovane Systems – Proprietary and Confidential</p>
    <div class="page-rule"></div>
    <span class="page-number">7</span>
  </footer>
</main>
</body>
</html>
```